Medical Billing Company Needs a Business Card Design

We need a business card design for a Florida based medical billing company called 'Clinicians Keystone Solutions'. We specialize in providing revenue cycle management services to physician and therapist offices (we're basically their back-office processing partner for providing billing software, claims submissions, A/R follow-up and patient statements & collections. Our logo is red and blue-ish, so make sure that whatever other elements are used will match appropriately. Our current business card design has a too small font size. I'd like to project an image that shows we are modern & reliable. On a side note, I'm planning on using ZUB for printing these cards.

Target Market(s)

Office managers, physicians, therapists

Industry/Entity Type

Printing

Requirements
Must have
• Logo
Name of Employee
Phone
Fax
E-mail
Website

```html
<!DOCTYPE html>
<html lang="en">
<head>
<meta charset="utf-8">
<title>Clinicians Keystone Solutions — Business Card</title>
<link rel="stylesheet" href="https://fonts.googleapis.com/css2?family=Open+Sans:wght@400;600;700&display=swap">
<style>
  :root {
    --backdrop: #ecebef;
    --card-white: #ffffff;
    --brand-navy: #2a1f6e;
    --brand-violet: #4b3a9a;
    --violet-light: #5d4ca6;
    --violet-deep: #1f0f72;
    --brand-red: #b01e2a;
    --ink: #3b3b45;
    --rule: #b9b9c2;
  }
  * { box-sizing: border-box; margin: 0; padding: 0; }
  html, body {
    width: 1200px; height: 720px; overflow: hidden;
    background: var(--backdrop);
    font-family: "Open Sans", Arial, sans-serif;
  }
  .canvas {
    width: 1200px; height: 720px;
    display: flex; align-items: center; justify-content: center; gap: 40px;
  }
  .card {
    position: relative;
    width: 540px; height: 309px;
    overflow: hidden;
    box-shadow: 0 6px 18px rgba(30, 20, 70, 0.18);
  }

  /* Front */
  .card-front { background: var(--card-white); }
  .brand-name {
    position: absolute; top: 54px; left: 0; width: 100%;
    text-align: center;
    font-size: 25px; font-weight: 600; letter-spacing: 2.5px;
    color: var(--brand-navy);
  }
  .contact-area {
    position: absolute; top: 116px; left: 0; width: 100%;
    display: flex; justify-content: center;
  }
  .person {
    text-align: right; padding-right: 14px; padding-top: 16px;
  }
  .person-name { font-size: 16px; font-weight: 700; color: var(--brand-violet); line-height: 1.2; }
  .person-title { font-size: 12px; color: var(--brand-red); line-height: 1.3; }
  .person-address { margin-top: 8px; font-size: 12px; color: var(--ink); line-height: 1.35; }
  .divider { width: 1px; background: var(--rule); }
  .contacts { list-style: none; padding-left: 14px; }
  .contacts li {
    display: flex; align-items: center; gap: 7px;
    font-size: 12px; color: var(--ink); line-height: 21px;
  }
  .contacts svg { width: 11px; height: 11px; flex: none; }
  .front-bands { position: absolute; left: 0; bottom: 0; width: 540px; height: 90px; }

  /* Back */
  .card-back {
    background: linear-gradient(135deg, var(--violet-light) 0%, var(--brand-violet) 45%, var(--violet-deep) 100%);
    color: #fff;
  }
  .back-name {
    position: absolute; top: 118px; left: 0; width: 100%;
    text-align: center; font-size: 24px; font-weight: 600; letter-spacing: 2.5px;
  }
  .back-url {
    position: absolute; bottom: 56px; left: 0; width: 100%;
    text-align: center; font-size: 14px; letter-spacing: 3.5px;
  }
</style>
</head>
<body>
<main class="canvas">
  <section class="card card-front" aria-label="Card front">
    <h1 class="brand-name">CLINICIANS KEYSTONE</h1>
    <div class="contact-area">
      <div class="person">
        <p class="person-name">Your Name</p>
        <p class="person-title">Title</p>
        <p class="person-address">Street Name, City Name<br>State Zip Code</p>
      </div>
      <div class="divider"></div>
      <ul class="contacts">
        <li>
          <svg viewBox="0 0 12 12" aria-hidden="true"><circle cx="6" cy="6" r="6" fill="var(--brand-navy)"/><path d="M4 3.2l1 1.4-.6.7c.4.9 1.1 1.6 2 2l.7-.6 1.4 1-.6 1.1C5.8 8.6 3.4 6.2 3.2 4z" fill="#fff"/></svg>
          123-456-0789
        </li>
        <li>
          <svg viewBox="0 0 12 12" aria-hidden="true"><rect x="3" y="0.5" width="6" height="11" rx="1.2" fill="var(--brand-navy)"/><rect x="4" y="2" width="4" height="6.5" fill="#fff"/></svg>
          123-456-0789
        </li>
        <li>
          <svg viewBox="0 0 12 12" aria-hidden="true"><circle cx="6" cy="6" r="6" fill="var(--brand-navy)"/><rect x="3" y="4" width="6" height="4.2" fill="#fff"/><path d="M3 4l3 2.3L9 4" stroke="var(--brand-navy)" stroke-width=".8" fill="none"/></svg>
          info@clinicianskeystone.com
        </li>
        <li>
          <svg viewBox="0 0 12 12" aria-hidden="true"><circle cx="6" cy="6" r="6" fill="var(--brand-navy)"/><g stroke="#fff" stroke-width=".8" fill="none"><circle cx="6" cy="6" r="3.4"/><ellipse cx="6" cy="6" rx="1.4" ry="3.4"/><path d="M2.6 6h6.8"/></g></svg>
          www.clinicianskeystone.com
        </li>
      </ul>
    </div>
    <svg class="front-bands" viewBox="0 0 540 90" preserveAspectRatio="none" aria-hidden="true">
      <polygon points="0,78 250,78 238,90 0,90" fill="var(--brand-red)"/>
      <polygon points="250,78 278,58 540,0 540,90 238,90" fill="var(--brand-violet)"/>
    </svg>
  </section>

  <section class="card card-back" aria-label="Card back">
    <p class="back-name">CLINICIANS KEYSTONE</p>
    <p class="back-url">www.clinicianskeystone.com</p>
  </section>
</main>
</body>
</html>
```